Business Card design for insurance broker in Denver, CO, USA

I need a business card designed using this logo that was just created. We sell life and disability income insurance to US consumers.
Looking for a professionally designed card to make use of the logo and have something to hand to prospects or new business referral sources. The card could be white, gray, black or whatever you would recommend.

Target Market(s)

US Consumers and other financial professionals that I partner with.

Industry/Entity Type

Insurance Broker

Contact Information for Business Card

Owen T. Farrow, CLU, LUTCF (please note that CLU should have a superscript R in a circle for registered trademark)
President
phone (303) 555-0187
email owen@keelbrookcover.example
4620 W. Halvern Rd, Suite 300, Larkfield Springs, CO 80999
Somewhere fit in a tagline saying "Your resource for life, long term care, and disability insurance" (maybe the back if it doesn't fit on the front, your call)

Font styles to use
Sans Serif

Requirements
Must have
• Must have logo in correct blue and gray colors, my name, address, phone, email. Order and placement determined by the designer.
• I just want something that looks a more professional than what I could have done using the business card designer tool on pixelbazaar.example or QuillPress, or any other do-it-yourself tool
• A regular rectangular business card with square corners is preferred
Nice to have
• I included the logos of 2 organizations I belong to (GKLS and WOBCE). They should be small, but visible on the back only. If it doesn’t look good, this is not a requirement, feel free to drop it.
Should not have
• Do not add any colors not already in the logo, except use of black and whites which are okay. If you use the logo on the back and want to make that in all black, gray or white, that may be okay as well.

```html
<!DOCTYPE html>
<html lang="en">
<head>
<meta charset="utf-8">
<title>Keelbrook Cover – Business Card</title>
<link href="https://fonts.googleapis.com/css2?family=Montserrat:wght@500;600&family=Lato:wght@400&display=swap" rel="stylesheet">
<style>
  :root{
    --blue:#4f83c5;
    --gray:#9e9e9e;
    --ink:#4a4a4a;
    --white:#ffffff;
    --backdrop:#e6e2db;
    --badge:#6e6e6e;
  }
  *{margin:0;padding:0;box-sizing:border-box}
  html,body{width:1200px;height:1200px;overflow:hidden;background:var(--backdrop)}
  .canvas{position:relative;width:1200px;height:1200px}
  .card{position:absolute;left:228px;width:744px;height:426px;border-radius:30px;overflow:hidden;box-shadow:0 14px 24px rgba(0,0,0,.18)}
  .card-back{top:147px;background:var(--gray)}
  .card-front{top:640px;background:var(--white)}

  /* wordmark */
  .wordmark{position:absolute;display:flex;align-items:center;gap:16px;font-family:"Montserrat",sans-serif;font-weight:600;letter-spacing:.5px;white-space:nowrap}
  .wordmark .mark{flex:none;background:var(--blue)}
  .card-back .wordmark{left:160px;top:125px;color:var(--white);font-size:44px}
  .card-back .wordmark .mark{width:22px;height:22px}
  .card-front .wordmark{right:26px;top:72px;color:var(--blue);font-size:34px}
  .card-front .wordmark .mark{width:18px;height:18px}

  .badges{position:absolute;top:248px;left:352px;display:flex;gap:46px;align-items:center}
  .badge-round{width:68px;height:68px;border-radius:50%;background:var(--badge)}
  .badge-square{width:68px;height:68px;background:var(--badge)}

  .tagline-band{position:absolute;left:0;right:0;top:369px;height:30px;background:var(--blue);color:var(--white);font-family:"Lato",sans-serif;font-size:17px;letter-spacing:.5px;text-align:center;line-height:30px}

  /* front */
  .name-tab{position:absolute;left:0;top:228px;width:14px;height:42px;background:var(--gray);border-radius:0 4px 4px 0}
  .person{position:absolute;left:26px;top:223px}
  .person-name{font-family:"Montserrat",sans-serif;font-weight:600;font-size:25px;color:var(--blue);letter-spacing:-.3px}
  .person-name .creds{color:var(--gray)}
  .person-name sup{font-size:12px}
  .person-title{font-family:"Lato",sans-serif;font-size:18px;color:var(--ink);letter-spacing:.5px}
  .rule{position:absolute;left:26px;right:26px;top:291px;height:1px;background:linear-gradient(90deg,var(--ink) 0 64%,var(--blue) 64% 100%)}
  .contacts{position:absolute;left:26px;top:314px;list-style:none;font-family:"Lato",sans-serif;font-size:18px;color:var(--ink);letter-spacing:.3px}
  .contacts li{display:flex;align-items:center;gap:10px;height:26px}
  .contacts svg{width:18px;height:18px;flex:none}
  .address{position:absolute;right:26px;top:314px;text-align:right;font-family:"Lato",sans-serif;font-size:18px;color:var(--ink);line-height:25px;letter-spacing:.3px;font-style:normal}
  .band-gray{position:absolute;left:0;top:400px;width:463px;height:26px;background:var(--gray)}
  .band-blue{position:absolute;left:471px;right:0;top:400px;height:26px;background:var(--blue)}
</style>
</head>
<body>
<main class="canvas">

  <section class="card card-back" aria-label="Card back">
    <div class="wordmark"><span class="mark"></span><span>Keelbrook Cover</span></div>
    <div class="badges">
      <div class="badge-round" role="img" aria-label="Membership badge"></div>
      <div class="badge-square" role="img" aria-label="Association membership badge"></div>
    </div>
    <p class="tagline-band">"Your resource for life, long term care, and disability insurance"</p>
  </section>

  <section class="card card-front" aria-label="Card front">
    <div class="wordmark"><span class="mark"></span><span>Keelbrook Cover</span></div>
    <span class="name-tab"></span>
    <div class="person">
      <p class="person-name">OWEN T. FARROW, <span class="creds">CLU<sup>®</sup>, &nbsp;LUTCF</span></p>
      <p class="person-title">President</p>
    </div>
    <div class="rule"></div>
    <ul class="contacts">
      <li><svg viewBox="0 0 18 18"><circle cx="9" cy="9" r="9" fill="#4f83c5"/><path d="M6 4.5l1.8 2.2-1 1.2a6 6 0 0 0 3.3 3.3l1.2-1 2.2 1.8-1 1.5C9 13.5 4.5 9 4.5 5.5z" fill="#fff"/></svg>(303) 555-0187</li>
      <li><svg viewBox="0 0 18 18"><circle cx="9" cy="9" r="9" fill="#4f83c5"/><rect x="4.5" y="5.8" width="9" height="6.4" rx="1" fill="#fff"/><path d="M4.8 6.2L9 9.3l4.2-3.1" stroke="#4f83c5" stroke-width="1" fill="none"/></svg>owen@keelbrookcover.example</li>
      <li><svg viewBox="0 0 18 18"><circle cx="9" cy="9" r="9" fill="#4f83c5"/><g stroke="#fff" stroke-width="1" fill="none"><circle cx="9" cy="9" r="4.5"/><ellipse cx="9" cy="9" rx="2" ry="4.5"/><path d="M4.5 9h9"/></g></svg>www.keelbrookcover.example</li>
    </ul>
    <address class="address">4620 W.<br>Halvern Rd, Suite 300<br>Larkfield Springs, CO 80999</address>
    <span class="band-gray"></span>
    <span class="band-blue"></span>
  </section>

</main>
</body>
</html>
```